Luxury Business Card Design for High-End Window Treatments

Gilded Slatworks
Custom Plantation Shutters & Architectural Shading Systems

⸻

BACK

Daniel Trevick
Owner

Custom Interior & Exterior Window Treatments

919-555-0148
gildedslatworks.com

I have included a picture that I’m hoping we can use on the back, but I’m also wondering if you can get rid of the ladder? Should we get rid of shutters , shades and blinds underneath Gilded Slatworks?

Target Market(s)

High-end residential homeowners, custom home builders, architects, interior designers, and luxury renovation clients seeking premium plantation shutters and motorized architectural shading systems.

Industry/Entity Type

Custom Window treatments

Contact Information for Business Card

Front Gilded Slatworks Custom Plantation Shutters Motorized Architectural Shading Systems BACK Daniel Trevick Owner 919-555-0148 GildedSlatworks.com Custom Interior & Exterior Window Treatments By Appointment

Requirements
Nice to have
• Not 100% sure on nice to halves or the color but you can definitely check out my website to get a better understanding of what I’m trying to do

```html
<!DOCTYPE html>
<html lang="en">
<head>
<meta charset="utf-8">
<title>Gilded Slatworks — Business Card</title>
<link href="https://fonts.googleapis.com/css2?family=Montserrat:wght@400;500;800&family=Playfair+Display:wght@400&display=swap" rel="stylesheet">
<style>
  :root {
    --backdrop: #1b1b1d;
    --card: #29292b;
    --card-deep: #222224;
    --gold: #fdd257;
    --cream: #efe9dc;
    --ink-light: #e9e9e9;
  }
  * { margin: 0; padding: 0; box-sizing: border-box; }
  html, body {
    width: 1200px; height: 952px; overflow: hidden;
    background: var(--backdrop);
  }
  .sheet {
    position: relative; width: 1200px; height: 952px;
    display: flex; flex-direction: column; align-items: center; justify-content: center; gap: 70px;
  }
  .card {
    position: relative; width: 600px; height: 343px; overflow: hidden;
    background: var(--card); border-radius: 4px;
    box-shadow: 0 18px 40px rgba(0,0,0,.45);
  }
  .brand-name {
    font-family: "Playfair Display", serif; font-weight: 400; color: var(--cream);
    line-height: 1;
  }
  .brand-name span { display: block; }
  .brand-name .second { padding-left: 0.9em; }
  .brand-tagline {
    font-family: "Playfair Display", serif; color: var(--gold);
    word-spacing: .55em; letter-spacing: .01em;
  }

  /* front */
  .front-photo {
    position: absolute; inset: 0;
    background:
      linear-gradient(90deg, rgba(255,255,255,.03) 0 2%, transparent 2% 24%, rgba(255,255,255,.035) 24% 26%, transparent 26% 48%, rgba(255,255,255,.035) 48% 50%, transparent 50%),
      linear-gradient(160deg, #333335 0%, #2a2a2c 45%, #202022 100%);
  }
  .front-tab-top {
    position: absolute; left: 0; top: 26px; width: 18px; height: 118px;
    background: var(--gold); border-radius: 0 9px 9px 0;
  }
  .front-tab-bottom {
    position: absolute; right: 0; bottom: 24px; width: 42px; height: 150px;
    background: var(--gold); border-radius: 12px 0 0 12px;
  }
  .front-brand { position: absolute; left: 150px; top: 96px; }
  .front-brand .brand-name { font-size: 56px; }
  .front-brand .brand-tagline { font-size: 21px; margin-top: 12px; }

  /* back */
  .back-brand { position: absolute; left: 38px; top: 92px; }
  .back-brand .brand-name { font-size: 38px; }
  .back-brand .brand-tagline { font-size: 15px; margin-top: 10px; }
  .contact { position: absolute; left: 330px; top: 92px; font-family: "Montserrat", sans-serif; color: var(--ink-light); }
  .contact-name { font-weight: 800; font-size: 25px; color: var(--gold); letter-spacing: .04em; text-transform: uppercase; }
  .contact-role { font-size: 13px; margin-top: 6px; }
  .contact-rule { width: 58px; height: 2px; background: var(--ink-light); margin: 7px 0 9px; }
  .contact-service { font-size: 10.5px; font-weight: 500; text-transform: uppercase; line-height: 1.35; letter-spacing: .02em; }
  .contact-list { list-style: none; margin-top: 12px; }
  .contact-list li { display: flex; align-items: center; gap: 8px; font-size: 12px; margin-bottom: 7px; }
  .contact-icon {
    width: 17px; height: 17px; border-radius: 3px; background: var(--gold);
    display: flex; align-items: center; justify-content: center;
  }
  .back-stripe { position: absolute; left: 0; bottom: 0; }
</style>
</head>
<body>
<main class="sheet">

  <section class="card card-front" aria-label="Card front">
    <div class="front-photo" role="img" aria-label="Faded dark photo of a room with tall windows dressed in plantation shutters"></div>
    <div class="front-tab-top"></div>
    <div class="front-tab-bottom"></div>
    <div class="front-brand">
      <h1 class="brand-name"><span>Gilded</span><span class="second">Slatworks</span></h1>
      <p class="brand-tagline">Shutters Shades Blinds</p>
    </div>
  </section>

  <section class="card card-back" aria-label="Card back">
    <div class="back-brand">
      <h2 class="brand-name"><span>Gilded</span><span class="second">Slatworks</span></h2>
      <p class="brand-tagline">Shutters Shades Blinds</p>
    </div>

    <div class="contact">
      <p class="contact-name">Daniel Trevick</p>
      <p class="contact-role">Owner</p>
      <div class="contact-rule"></div>
      <p class="contact-service">Custom Interior &amp; Exterior<br>Window Treatments</p>
      <ul class="contact-list">
        <li>
          <span class="contact-icon">
            <svg width="11" height="11" viewBox="0 0 24 24"><path fill="#29292b" d="M6.6 10.8a15.1 15.1 0 0 0 6.6 6.6l2.2-2.2c.3-.3.7-.4 1-.2 1.1.4 2.3.6 3.6.6.6 0 1 .4 1 1V20c0 .6-.4 1-1 1A17 17 0 0 1 3 4c0-.6.4-1 1-1h3.5c.6 0 1 .4 1 1 0 1.3.2 2.5.6 3.6.1.3 0 .7-.2 1z"/></svg>
          </span>
          919-555-0148
        </li>
        <li>
          <span class="contact-icon">
            <svg width="12" height="12" viewBox="0 0 24 24" fill="none" stroke="#29292b" stroke-width="2"><circle cx="12" cy="12" r="9"/><path d="M3 12h18M12 3c3 3 3 15 0 18M12 3c-3 3-3 15 0 18"/></svg>
          </span>
          gildedslatworks.com
        </li>
      </ul>
    </div>

    <svg class="back-stripe" width="600" height="343" viewBox="0 0 600 343">
      <rect x="0" y="276" width="282" height="3" fill="var(--cream)"/>
      <polygon points="290,272 600,272 600,284 300,284" fill="var(--gold)"/>
    </svg>
  </section>

</main>
</body>
</html>
```